Client Meeting and installation Email Follow up

I would like a follow-up email template created.
Currently, we do a lot of new construction builds and meet with clients about 6-3 months before they take possession of their new house. I want a follow-up email template to be sent after the homeowner takes possession of their house that enquires if the clients are happy about their new lighting, the service they received, and their customer service representative with Brightwell Lamps and Breezes. I have attached a few files of what our current marketing looks like.
Target Market(s)
Home Owners We have already met with
Industry/Entity Type
Residential lighting
Font styles to use
Other font styles liked:
- Alta Light, Playfair Display, Montserrat
Colors
Designer to choose colors to be used in the design.
Look and feel
Each slider illustrates characteristics of the customer's brand and the style your logo design should communicate.

```html
<!DOCTYPE html>
<html lang="en">
<head>
<meta charset="utf-8">
<title>Brightwell Lamps and Breezes – Post-Installation Follow Up</title>
<link rel="stylesheet" href="https://fonts.googleapis.com/css2?family=Open+Sans:wght@400;500;600;700&family=Poppins:wght@700;800&display=swap">
<style>
  :root{
    --orange:#f7941d;
    --orange-deep:#f57f0f;
    --orange-light:#f6b42a;
    --ink:#161616;
    --night:#121212;
    --grey-text:#6a6a6a;
    --rule:#9a9a9a;
    --white:#ffffff;
  }
  *{box-sizing:border-box;margin:0;padding:0}
  html,body{width:1200px;height:3740px;overflow:hidden;background:var(--white)}
  body{position:relative;font-family:"Open Sans",Arial,sans-serif;color:var(--ink)}
  .abs{position:absolute}

  /* Header */
  .top-bar{left:0;top:0;width:1200px;height:39px;background:var(--orange)}
  .brand{left:0;top:12px;width:1200px;text-align:center}
  .brand-name{display:inline-flex;align-items:center;gap:12px;background:var(--white);padding:10px 20px;font-family:"Open Sans",Arial,sans-serif;font-weight:600;font-size:30px;color:var(--ink);letter-spacing:1px}
  .brand-mark{width:16px;height:16px;background:var(--ink)}

  /* Hero */
  .hero{left:0;top:108px;width:1200px;height:630px}
  .hero-badge{left:705px;top:182px;width:366px;height:366px;border-radius:50%;
    background:radial-gradient(circle at 60% 40%,var(--orange-light),var(--orange-deep));
    display:flex;align-items:center;justify-content:center;text-align:center;
    font-family:"Poppins",Arial,sans-serif;font-weight:800;font-size:36px;line-height:57px;color:var(--ink)}

  /* Intro */
  .intro-photo{left:94px;top:805px;width:430px;height:430px;border-radius:50%;border:5px solid var(--orange);padding:7px;background:var(--white)}
  .intro-photo div{width:100%;height:100%;border-radius:50%;background:radial-gradient(circle at 45% 45%,#f4c77a 0%,#9a8a7c 35%,#6d7f92 70%,#4f6070 100%)}
  .greeting{left:597px;top:868px;display:flex;align-items:flex-end;gap:30px}
  .greeting .dear{font-size:24px;color:var(--ink)}
  .greeting .name-field{width:198px;border-bottom:1px solid #c9c9c9;font-size:15px;letter-spacing:6px;color:#555;padding-bottom:6px}
  .intro-copy{left:600px;top:926px;width:545px;font-size:17px;line-height:33px;color:var(--grey-text)}
  .intro-copy p+p{margin-top:33px}

  /* Feedback */
  .feedback{left:0;top:1315px;width:1200px;height:1313px;background:radial-gradient(ellipse at 50% 45%,#262626 0%,var(--night) 70%,#0b0b0b 100%);color:var(--white)}
  .feedback-title{position:absolute;left:0;top:102px;width:1200px;text-align:center;font-size:28px;line-height:44px;font-weight:700;letter-spacing:.3px}
  .feedback-title::after{content:"";display:block;width:100px;height:4.5px;background:var(--orange);margin:14px auto 0}
  .groups{position:absolute;left:134px;top:233px;width:932px}
  .group{height:332px}
  .group-head{height:60px;display:flex;align-items:center;gap:20px;margin-left:1px}
  .group-icon{width:62px;height:62px;border-radius:50%;background:var(--orange);border:2px solid #ffd27a;display:flex;align-items:center;justify-content:center}
  .group-title{font-size:24px;font-weight:600}
  .question{font-size:18px;font-weight:500;line-height:27px;margin-top:22px}
  .question:first-of-type{margin-top:22px}
  .answer{height:55px;background:var(--white);border-radius:6px;margin-top:14px}
  .group-head + .question{margin-top:22px}

  /* Closing */
  .closing{left:110px;top:2687px;width:980px;text-align:center;font-size:25.5px;line-height:42px;font-weight:600;color:var(--ink)}
  .signoff-left{left:75px;top:3029px;width:290px}
  .rule{border-top:1.5px solid var(--rule)}
  .company-line{text-align:center;font-size:18px;margin-top:16px}
  .contact-label{font-size:21px;margin-top:26px;width:320px}
  .signoff-left .rule.l2{margin-top:36px}
  .signoff-left .rule.l3{margin-top:48px}
  .signoff-right{left:834px;top:3008px;width:294px}
  .regards{font-size:21px}
  .sig-field{margin-left:3px;margin-top:18px;border-bottom:1.5px solid var(--rule);font-size:16px;color:#555;padding:0 0 4px 8px}
  .sig-field+.sig-field{margin-top:40px;padding-left:0}

  /* Footer */
  .footer-shape{left:0;top:3240px;width:1200px;height:500px}
  .footer-col{top:3413px}
  .footer-head{display:flex;align-items:center;gap:10px;font-size:24px;font-weight:600;color:var(--ink)}
  .footer-body{font-size:21px;line-height:33px;margin-top:15px;color:var(--ink)}
  .col-location{left:128px}
  .col-phone{left:531px}
  .col-hours{left:893px}
  .copyright{left:135px;top:3628px;font-size:21px}
</style>
</head>
<body>

<header>
  <div class="abs top-bar"></div>
  <div class="abs brand"><span class="brand-name"><span class="brand-mark"></span>Brightwell Lamps and Breezes</span></div>
</header>

<section class="abs hero">
  <svg width="1200" height="630" viewBox="0 0 1200 630">
    <defs>
      <linearGradient id="room" x1="0" y1="0" x2="1" y2="1">
        <stop offset="0" stop-color="#23324a"/>
        <stop offset=".45" stop-color="#3b4d6a"/>
        <stop offset="1" stop-color="#6f86ab"/>
      </linearGradient>
      <radialGradient id="lamp" cx=".2" cy=".4" r=".35">
        <stop offset="0" stop-color="#f3d9a8" stop-opacity=".8"/>
        <stop offset="1" stop-color="#f3d9a8" stop-opacity="0"/>
      </radialGradient>
    </defs>
    <g role="img" aria-label="Photo of a woman reading in bed beside a glowing bedside lamp">
      <rect width="1200" height="630" fill="url(#room)"/>
      <rect width="1200" height="630" fill="url(#lamp)"/>
    </g>
    <path d="M0 550 Q600 700 1200 545 L1200 630 L0 630 Z" fill="var(--white)"/>
    <path d="M0 545 Q600 680 1200 540 L1200 585 Q600 675 0 575 Z" fill="var(--orange)"/>
  </svg>
</section>
<div class="abs hero-badge">WE HOPE YOU’RE<br>LOVING YOUR NEW<br>LIGHTING!</div>

<section>
  <div class="abs intro-photo"><div role="img" aria-label="Photo of a hand adjusting pendant bulbs in geometric wire cages"></div></div>
  <div class="abs greeting"><span class="dear">Dear Client</span><span class="name-field">YOUR NAME</span></div>
  <div class="abs intro-copy">
    <p>Congratulations on the recent move into your new home! We hope you’re settling in well and enjoying your new space.</p>
    <p>At Brightwell Lamps and Breezes, we’re dedicated to ensuring that every detail of your lighting installation meets your expectations. We’d love to hear about your experience with our services and the installation process.</p>
  </div>
</section>

<section class="abs feedback">
  <h2 class="feedback-title">HERE ARE A FEW THINGS WE’D APPRECIATE<br>YOUR FEEDBACK ON</h2>
  <div class="groups">
    <div class="group">
      <div class="group-head">
        <span class="group-icon"><svg width="32" height="32" viewBox="0 0 32 32" fill="none" stroke="#3a2a10" stroke-width="1.8" stroke-linecap="round"><circle cx="16" cy="12" r="7"/><path d="M13 19v4h6v-4M14 26h4"/></svg></span>
        <span class="group-title">Your Satisfaction with the Lighting</span>
      </div>
      <p class="question">1 . Are you pleased with how the lighting enhances your new home?</p>
      <div class="answer"></div>
      <p class="question">2 . Are there any adjustments or additional features you would like to discuss?</p>
      <div class="answer"></div>
    </div>
    <div class="group">
      <div class="group-head">
        <span class="group-icon"><svg width="32" height="32" viewBox="0 0 32 32" fill="none" stroke="#3a2a10" stroke-width="1.8" stroke-linecap="round"><path d="M7 25l11-11M18 14a5 5 0 1 0 5-7l-3 3-3-1-1-3 3-3"/><path d="M25 25L15 15"/></svg></span>
        <span class="group-title">The Installation Process</span>
      </div>
      <p class="question">1 . Did our team meet your expectations during the installation ?</p>
      <div class="answer"></div>
      <p class="question">2 . Was the process smooth and professional?</p>
      <div class="answer"></div>
    </div>
    <div class="group">
      <div class="group-head">
        <span class="group-icon"><svg width="32" height="32" viewBox="0 0 32 32" fill="none" stroke="#3a2a10" stroke-width="1.8" stroke-linecap="round"><circle cx="11" cy="11" r="4"/><circle cx="21" cy="11" r="4"/><path d="M4 25c0-5 3-8 7-8s7 3 7 8M14 25c0-5 3-8 7-8s7 3 7 8"/></svg></span>
        <span class="group-title">Customer Service Experience</span>
      </div>
      <p class="question">1 . How did you find working with your Brightwell Lamps and Breezes representative?</p>
      <div class="answer"></div>
      <p class="question">2 . Were they helpful and responsive to your needs?</p>
      <div class="answer"></div>
    </div>
  </div>
</section>

<section>
  <p class="abs closing">Your feedback is invaluable to us as it helps us continually improve our services. If there’s anything you’d like to discuss or if you need further assistance, please don’t hesitate to reach out.<br>Thank you for choosing Brightwell Lamps and Breezes for your new home. We look forward to hearing from you and hope you continue to enjoy your beautifully lit space!</p>

  <div class="abs signoff-left">
    <div class="rule"></div>
    <p class="company-line">Brightwell Lamps and Breezes</p>
    <p class="contact-label">YOUR CONTACT INFORMATION</p>
    <div class="rule l2"></div>
    <div class="rule l3"></div>
  </div>

  <div class="abs signoff-right">
    <p class="regards">Best regards,</p>
    <p class="sig-field">Your Name</p>
    <p class="sig-field">Your Position</p>
  </div>
</section>

<footer>
  <svg class="abs footer-shape" width="1200" height="500" viewBox="0 3240 1200 500">
    <defs>
      <linearGradient id="foot" x1="0" y1="0" x2="1" y2="0">
        <stop offset="0" stop-color="var(--orange-light)"/>
        <stop offset="1" stop-color="var(--orange-deep)"/>
      </linearGradient>
    </defs>
    <path d="M0 3375 Q600 3219 1200 3375 L1200 3740 L0 3740 Z" fill="url(#foot)"/>
    <path d="M0 3335 Q600 3251 1200 3335 L1200 3375 Q600 3219 0 3375 Z" fill="#000"/>
  </svg>

  <div class="abs footer-col col-location">
    <div class="footer-head"><svg width="16" height="22" viewBox="0 0 16 22"><path d="M8 0a8 8 0 0 0-8 8c0 6 8 14 8 14s8-8 8-14a8 8 0 0 0-8-8zm0 11a3 3 0 1 1 0-6 3 3 0 0 1 0 6z" fill="var(--ink)"/></svg>Location</div>
    <div class="footer-body">1820 Larkspur Avenue S.E<br>Calgary, AB T2G 4K1 CA</div>
  </div>
  <div class="abs footer-col col-phone">
    <div class="footer-head"><svg width="20" height="20" viewBox="0 0 24 24"><path d="M6.6 10.8a15 15 0 0 0 6.6 6.6l2.2-2.2c.3-.3.7-.4 1-.2 1.1.4 2.3.6 3.6.6.6 0 1 .4 1 1V20c0 .6-.4 1-1 1A17 17 0 0 1 3 4c0-.6.4-1 1-1h3.5c.6 0 1 .4 1 1 0 1.3.2 2.5.6 3.6.1.3 0 .7-.2 1z" fill="var(--ink)"/></svg>Phone Number</div>
    <div class="footer-body">403.555.0187</div>
  </div>
  <div class="abs footer-col col-hours">
    <div class="footer-head"><svg width="20" height="20" viewBox="0 0 20 20" fill="none" stroke="var(--ink)" stroke-width="2.2"><circle cx="10" cy="10" r="8"/><path d="M10 5v5h4"/></svg>Hours</div>
    <div class="footer-body">Mon: 9AM-5:30PM<br>Tues: 9AM-5:30PM<br>Wed: 9AM-5:30PM<br>Thurs: 9AM-7PM<br>Fri: 9AM-5:30PM<br>Sat: 9:30AM-5PM<br>Sun: Closed</div>
  </div>
  <p class="abs copyright">© 2024 Brightwell Lamps . All Rights Reserved</p>
</footer>

</body>
</html>
```